Business card design for Virtual Assistance company

I need a business card designed for my virtual assistance company. We are a small company who services primarily C-level executive clients. The card needs to be double sided with the following contact information on the back:
Melissa Thornbury
Owner/CEO
info@rkpadvisory.net
www.rkpadvisory.net
555.302.9817

The front side should just have the company name incorporated: "RKP Advisory" and "virtual assistance"

The card should be simplistic, but eye catching and should speak to high level executives. Our primary focus areas consist of executive assistance and government contracting.

Target Market(s)

CEOs and executives

Contact Information for Business Card

see project description. phone, email, website.

Colors

Designer to choose only greyscale colors for use in the design.

```html
<!DOCTYPE html>
<html lang="en">
<head>
<meta charset="utf-8">
<title>RKP Advisory – Business Card</title>
<link href="https://fonts.googleapis.com/css2?family=Cinzel:wght@600&family=Poppins:wght@400;500&display=swap" rel="stylesheet">
<style>
  :root {
    --backdrop: #5e5e5e;
    --card: #121212;
    --accent: #c4c4c4;
    --white: #ffffff;
    --muted: #8c8c8c;
    --silver: #9e9e9e;
  }
  * { margin: 0; padding: 0; box-sizing: border-box; }
  html, body { width: 1043px; height: 1200px; overflow: hidden; }
  body { background: var(--backdrop); position: relative; font-family: "Poppins", sans-serif; }

  .card { position: absolute; left: 215px; width: 568px; height: 351px; background: var(--card); }
  .card--contact { top: 222px; }
  .card--brand { top: 606px; display: flex; flex-direction: column; align-items: center; justify-content: center; }

  .holder { position: absolute; left: 0; top: 192px; height: 52px; padding-left: 25px; border-left: 7px solid var(--accent); }
  .holder__name { font-family: "Cinzel", serif; font-weight: 600; font-size: 20.5px; color: var(--accent); line-height: 1.2; padding-top: 6px; white-space: nowrap; }
  .holder__role { font-size: 16px; color: var(--white); line-height: 1.2; }

  .contacts { position: absolute; right: 44px; top: 263px; list-style: none; }
  .contacts li { display: flex; align-items: center; justify-content: flex-end; gap: 9px; height: 20.5px; font-size: 17px; color: var(--white); white-space: nowrap; }
  .contacts svg { width: 15px; height: 15px; fill: none; stroke: var(--accent); stroke-width: 2; flex: none; }
  .contacts .icon-solid { fill: var(--accent); stroke: none; }

  .brand__name { font-family: "Cinzel", serif; font-weight: 600; font-size: 60px; line-height: 1; color: var(--silver); letter-spacing: 2px; white-space: nowrap; }
  .brand__tagline { display: flex; align-items: center; gap: 8px; width: 300px; margin-top: 16px; color: var(--muted); font-size: 12px; font-weight: 500; letter-spacing: 1.8px; text-transform: uppercase; white-space: nowrap; }
  .brand__tagline::before, .brand__tagline::after { content: ""; flex: 1; height: 1.5px; background: var(--muted); }
</style>
</head>
<body>
  <section class="card card--contact">
    <div class="holder">
      <p class="holder__name">MELISSA THORNBURY</p>
      <p class="holder__role">Owner/CEO</p>
    </div>

    <ul class="contacts">
      <li>555.302.9817
        <svg viewBox="0 0 16 16" aria-hidden="true"><path d="M3 2.5l2.5-.5 1.5 3-1.5 1.2a8 8 0 0 0 4 4L10.7 8.7l3 1.5-.5 2.5c-6 .8-11-4.2-10.2-10.2z"/><path d="M9.5 2.5a4 4 0 0 1 4 4M9.5 0.5a6 6 0 0 1 6 6" stroke-width="1.4"/></svg>
      </li>
      <li>info@rkpadvisory.net
        <svg viewBox="0 0 16 16" aria-hidden="true"><rect class="icon-solid" x="0.5" y="3" width="15" height="10.5"/><path d="M1 3.5l7 5.5 7-5.5M1 13l5-4.5M15 13l-5-4.5" stroke="#121212" stroke-width="1.2"/></svg>
      </li>
      <li>www.rkpadvisory.net
        <svg viewBox="0 0 16 16" aria-hidden="true"><circle cx="8" cy="8" r="6.6"/><ellipse cx="8" cy="8" rx="3" ry="6.6" stroke-width="1.4"/><path d="M1.5 8h13M2.5 5h11M2.5 11h11" stroke-width="1.2"/></svg>
      </li>
    </ul>
  </section>

  <section class="card card--brand">
    <p class="brand__name">RKP ADVISORY</p>
    <p class="brand__tagline">Virtual Assistance</p>
  </section>
</body>
</html>
```